The quiet harbor with an elephant incorporated in the background

Target Market(s)

Real estate

Industry/Entity Type

Real Estate

Contact Information for Business Card

On back on want my name & number
In front I want the business name, "the quiet harbor", below to say staging & design

Logo Text

The quiet harbor

Font styles to use
Serif

Colors
000000

Requirements
Must have
• I want an elephant behind the writing in gold transperant

```html
<!DOCTYPE html>
<html lang="en">
<head>
<meta charset="utf-8">
<title>The Quiet Harbor – Business Card</title>
<link rel="stylesheet" href="https://fonts.googleapis.com/css2?family=Cinzel:wght@400;600&family=Raleway:wght@300&family=Open+Sans:wght@400&display=swap">
<style>
  :root {
    --page-bg: #2f2b29;
    --card-dark: #1d1c1c;
    --card-gold: #fdb400;
    --gold-text: #f6b20a;
    --gold-deep: #e29d06;
    --gold-light: #f9c64a;
    --elephant-faint: rgba(110, 86, 30, 0.45);
    --tagline: #8a8680;
    --contact: #f2f0ec;
    --white: #ffffff;
  }
  * { margin: 0; padding: 0; box-sizing: border-box; }
  html, body {
    width: 1200px; height: 844px; overflow: hidden;
    background: var(--page-bg);
  }
  .stage {
    position: relative; width: 1200px; height: 844px;
    display: flex; align-items: center; justify-content: center; gap: 40px;
  }
  .card {
    position: relative; width: 540px; height: 310px; overflow: hidden;
    box-shadow: 0 14px 30px rgba(0,0,0,0.45);
  }
  /* Back: contact side */
  .card--back { background: var(--card-dark); }
  .elephant-faint {
    position: absolute; left: 250px; top: 130px; width: 260px; height: 180px;
    border-radius: 48% 52% 0 0 / 60% 60% 0 0;
    background: radial-gradient(ellipse at 45% 40%, var(--elephant-faint), rgba(110,86,30,0.15) 75%);
  }
  .brand-mark {
    position: absolute; left: 268px; top: 30px;
    width: 26px; height: 26px; background: var(--gold-text);
  }
  .brand-name {
    position: absolute; right: 34px; top: 70px;
    font-family: "Cinzel", serif; font-weight: 400; font-size: 27px;
    color: var(--gold-text); letter-spacing: 0.5px; white-space: nowrap;
  }
  .brand-tagline {
    position: absolute; right: 48px; top: 108px;
    font-family: "Raleway", sans-serif; font-weight: 300; font-size: 15px;
    color: var(--tagline); letter-spacing: 1px;
  }
  .person-name {
    position: absolute; left: 30px; top: 170px;
    font-family: "Cinzel", serif; font-weight: 600; font-size: 21px;
    color: var(--gold-text);
  }
  .contact-list {
    position: absolute; left: 30px; top: 208px; list-style: none;
    font-family: "Open Sans", sans-serif; font-size: 13.5px; line-height: 20px;
    color: var(--contact);
  }
  .contact-list li { display: flex; align-items: center; gap: 8px; }
  .contact-list .address { padding-left: 0; margin-top: 8px; display: block; }
  .contact-icon { width: 11px; height: 11px; fill: var(--gold-text); flex: none; }

  /* Front: brand side */
  .card--front { background: var(--card-gold); }
  .elephant-gold {
    position: absolute; left: 60px; top: 30px; width: 440px; height: 300px;
    border-radius: 45% 55% 0 0 / 55% 60% 0 0;
    background: linear-gradient(100deg, var(--gold-light) 0%, var(--gold-deep) 55%, var(--gold-light) 100%);
    opacity: 0.75;
  }
  .front-lockup {
    position: absolute; left: 0; right: 0; top: 122px;
    display: flex; align-items: center; justify-content: center; gap: 14px;
  }
  .front-mark { width: 34px; height: 34px; background: var(--white); }
  .front-name {
    font-family: "Cinzel", serif; font-weight: 600; font-size: 34px;
    color: var(--white); white-space: nowrap;
  }
</style>
</head>
<body>
<main class="stage">
  <section class="card card--back" aria-label="Contact side">
    <div class="elephant-faint" role="img" aria-label="Faint gold elephant silhouette in the background"></div>
    <div class="brand-mark" aria-hidden="true"></div>
    <h1 class="brand-name">The Quiet Harbor</h1>
    <p class="brand-tagline">staging &amp; design</p>
    <h2 class="person-name">Daniel Reed</h2>
    <ul class="contact-list">
      <li>
        <svg class="contact-icon" viewBox="0 0 24 24" aria-hidden="true"><path d="M6.6 10.8a15.1 15.1 0 0 0 6.6 6.6l2.2-2.2c.3-.3.7-.4 1-.2 1.1.4 2.3.6 3.6.6.6 0 1 .4 1 1V20c0 .6-.4 1-1 1A17 17 0 0 1 3 4c0-.6.4-1 1-1h3.5c.6 0 1 .4 1 1 0 1.3.2 2.5.6 3.6.1.3 0 .7-.2 1z"/></svg>
        (044)555018244
      </li>
      <li>
        <svg class="contact-icon" viewBox="0 0 24 24" aria-hidden="true"><path d="M2 5h20v14H2z M2 5l10 8 10-8" /></svg>
        info@quietharbor.com
      </li>
      <li class="address">1234, Address GoesHere,<br>Country name, 12345</li>
    </ul>
  </section>

  <section class="card card--front" aria-label="Brand side">
    <div class="elephant-gold" role="img" aria-label="Large gold elephant silhouette behind the name"></div>
    <div class="front-lockup">
      <div class="front-mark" aria-hidden="true"></div>
      <span class="front-name">The Quiet Harbor</span>
    </div>
  </section>
</main>
</body>
</html>
```